Velundra Jobs portal

Velundra Jobs is a job portal connecting job seekers and companies offering part time jobs in the Mena region, starting in the UAE. We would like to see designs that use the color blue. We have attached images to give an idea what the website should look like. When a company posts a job the job seekers are not allowed to see which company has posted a job. There should also be a coinvex gateway. On the landing page we want a catching picture that we will send.

Target Market(s)

Students and promotional workers

Logo Text

Velundra Jobs

Coding

Coded - Design and coding required

Number of Pages Required

4 page

Font styles to use
Sans Serif

Colors
33a6d7
0692cd
85cae6

```html
<!DOCTYPE html>
<html lang="en">
<head>
<meta charset="utf-8">
<title>Velundra Jobs</title>
<link href="https://fonts.googleapis.com/css2?family=Arimo:wght@400;700&display=swap" rel="stylesheet">
<style>
:root{
  --purple:#7d3c98;
  --purple-btn:#7c419b;
  --teal:#52c2c3;
  --blue-btn:#4a74b8;
  --logo:#33a6d7;
  --panel:#f6f6f6;
  --line:#d4d4d4;
  --text:#555555;
  --muted:#7a7a7a;
  --faint:#f1f1f1;
  --white:#ffffff;
}
*{margin:0;padding:0;box-sizing:border-box}
html,body{width:1200px;height:971px;overflow:hidden;background:var(--white);font-family:"Arimo",Arial,sans-serif;color:var(--text)}
.page{position:relative;width:1200px;height:971px}
.abs{position:absolute;white-space:nowrap}

.site-header{position:absolute;left:0;top:0;width:1200px;height:89px;background:var(--panel);border-bottom:2px solid #e6e6e6}
.brand{left:130px;top:16px;font-size:44px;color:var(--logo);letter-spacing:0.5px;line-height:52px}
.top-nav{left:334px;top:38px;font-size:14px;color:#444;display:flex;gap:14px;letter-spacing:.3px}
.icon-search{left:812px;top:31px}
.icon-bell{left:858px;top:26px}
.badge{left:876px;top:26px;width:21px;height:21px;border-radius:50%;background:var(--purple);color:var(--white);font-size:11px;font-weight:700;text-align:center;line-height:21px}
.avatar{left:910px;top:22px;width:51px;height:51px;border-radius:50%;background:linear-gradient(135deg,#c9936c,#5a3a2a)}
.btn-logout{left:986px;top:33px;width:82px;height:30px;border-radius:3px;background:#9a9a9a;color:var(--white);font-size:14px;text-align:center;line-height:30px;letter-spacing:.3px}

.category{left:130px;width:220px;height:41px;border:1px solid var(--line);border-radius:3px;background:var(--white);font-size:13.5px;letter-spacing:.4px;color:var(--text);display:flex;justify-content:space-between;align-items:center;padding:2px 15px 0 18px}

.filter-panel{left:370px;top:138px;width:700px;height:93px;background:var(--panel);border-radius:3px}
.field{top:167px;height:39px;background:var(--white);border:1px solid #e0e0e0;border-radius:2px;font-size:14px;letter-spacing:.3px;line-height:39px;padding-left:19px}
.field-keywords{left:400px;width:257px;color:#9a9a9a}
.field-district{left:673px;width:212px;color:var(--purple)}
.field-district::after{content:"";position:absolute;right:16px;top:16px;border-left:5px solid transparent;border-right:5px solid transparent;border-top:6px solid #888}
.btn-filter{left:902px;top:167px;width:133px;height:39px;border-radius:3px;background:var(--purple-btn);color:var(--white);font-size:15px;font-weight:700;letter-spacing:.3px;text-align:center;line-height:39px}

.col-head{color:var(--purple);font-size:14px;letter-spacing:.3px}
.col-head-title{left:403px;top:268px;font-size:19px}
.job-row{left:370px;width:700px;height:67px;background:var(--panel)}
.job-row.is-active{background:var(--teal)}
.job-row span{position:absolute;top:3px;line-height:67px;color:var(--muted)}
.job-row.is-active span{color:var(--white)}
.job-title{left:26px;font-size:19px;letter-spacing:.4px}
.job-date{left:277px;font-size:13.5px;font-weight:700;letter-spacing:.6px}
.job-location{left:436px;font-size:13.5px;font-weight:700;letter-spacing:.6px}
.job-row .btn-apply{left:569px;top:19px;width:111px;height:33px;border-radius:3px;background:var(--blue-btn);color:var(--white);font-size:14px;font-weight:700;text-align:center;line-height:33px;letter-spacing:.2px}

.section-title{left:375px;top:645px;font-size:21px;font-weight:400;letter-spacing:.5px;color:var(--purple)}
.job-photo{top:690px;width:112px;height:112px}

.mascot-area{left:100px;top:710px;width:215px;height:261px;background:linear-gradient(180deg,#f5f5f5,#f0f0f0);border-radius:60px 60px 20px 20px}

.footer-copy{left:175px;top:922px;font-size:14px;letter-spacing:.3px;color:var(--purple)}
.footer-links{right:131px;top:920px;font-size:14px;letter-spacing:.3px;color:var(--purple)}
</style>
</head>
<body>
<div class="page">
  <header class="site-header">
    <div class="abs brand">velundra</div>
    <nav class="abs top-nav"><span>About Us</span><span>|</span><span>Contact Us</span></nav>
    <svg class="abs icon-search" width="32" height="32" viewBox="0 0 32 32"><circle cx="13" cy="13" r="10" fill="none" stroke="#111" stroke-width="2"/><line x1="20" y1="20" x2="30" y2="30" stroke="#111" stroke-width="2.5"/></svg>
    <svg class="abs icon-bell" width="34" height="40" viewBox="0 0 34 40"><path d="M7 30 Q9 27 9 20 Q9 11 17 10 Q25 11 25 20 Q25 27 28 30 Z" fill="none" stroke="#111" stroke-width="2"/><path d="M13 33 Q17 38 21 33" fill="none" stroke="#111" stroke-width="2"/></svg>
    <div class="abs badge">23</div>
    <div class="abs avatar" role="img" aria-label="Profile photo of the signed-in user"></div>
    <div class="abs btn-logout">Log out</div>
  </header>

  <div class="abs mascot-area" role="img" aria-label="Faint mascot illustration"></div>

  <aside>
    <div class="abs category" style="top:138px"><span>Categorie 1</span><span>(33)</span></div>
    <div class="abs category" style="top:189px"><span>Categorie 2</span><span>(33)</span></div>
    <div class="abs category" style="top:240px"><span>Categorie 3</span><span>(33)</span></div>
    <div class="abs category" style="top:292px"><span>Categorie 4</span><span>(33)</span></div>
    <div class="abs category" style="top:343px"><span>Categorie 5</span><span>(33)</span></div>
    <div class="abs category" style="top:395px"><span>Categorie 6</span><span>(33)</span></div>
    <div class="abs category" style="top:447px"><span>Categorie 7</span><span>(33)</span></div>
    <div class="abs category" style="top:499px"><span>Categorie 8</span><span>(33)</span></div>
    <div class="abs category" style="top:551px"><span>Categorie 9</span><span>(33)</span></div>
    <div class="abs category" style="top:601px"><span>Categorie 10</span><span>(33)</span></div>
  </aside>

  <section>
    <div class="abs filter-panel"></div>
    <div class="abs field field-keywords">Keywords</div>
    <div class="abs field field-district">District 1</div>
    <div class="abs btn-filter">Filter Jobs</div>

    <div class="abs col-head col-head-title">Job Title</div>
    <div class="abs col-head" style="left:660px;top:273px">Due date</div>
    <div class="abs col-head" style="left:806px;top:273px">Location</div>

    <div class="abs job-row is-active" style="top:303px"><span class="job-title">Job title number 1</span><span class="job-date">23 Jan 2015</span><span class="job-location">District 1</span><span class="btn-apply">Apply Now</span></div>
    <div class="abs job-row" style="top:376px"><span class="job-title">Job title number 1</span><span class="job-date">23 Jan 2015</span><span class="job-location">District 1</span><span class="btn-apply">Apply Now</span></div>
    <div class="abs job-row" style="top:450px"><span class="job-title">Job title number 1</span><span class="job-date">23 Jan 2015</span><span class="job-location">District 1</span><span class="btn-apply">Apply Now</span></div>
    <div class="abs job-row" style="top:524px"><span class="job-title">Job title number 1</span><span class="job-date">23 Jan 2015</span><span class="job-location">District 1</span><span class="btn-apply">Apply Now</span></div>
  </section>

  <section>
    <h2 class="abs section-title">Featured Part Time Jobs</h2>
    <div class="abs job-photo" style="left:375px;background:linear-gradient(180deg,#e8ecef,#a9adb3)" role="img" aria-label="Photo for a featured part time job"></div>
    <div class="abs job-photo" style="left:520px;background:linear-gradient(180deg,#e9eef2,#c9b9a6)" role="img" aria-label="Photo for a featured part time job"></div>
    <div class="abs job-photo" style="left:667px;background:linear-gradient(180deg,#e4e1dc,#787c84)" role="img" aria-label="Photo for a featured part time job"></div>
    <div class="abs job-photo" style="left:813px;background:linear-gradient(180deg,#eef2f5,#7e8ea3)" role="img" aria-label="Photo for a featured part time job"></div>
    <div class="abs job-photo" style="left:957px;background:linear-gradient(180deg,#9ea4a8,#9fbedc)" role="img" aria-label="Photo for a featured part time job"></div>
  </section>

  <footer>
    <div class="abs footer-copy">Copyright reserved to velundra 2015</div>
    <div class="abs footer-links">About Us - terms &amp; conditions - sitemap</div>
  </footer>
</div>
</body>
</html>
```